Optometry need some pictures for business card

I am interested in getting the 3 pictures below in minimum 300dpi created as close as possible to the original image for our businesss sized magnets. Cannot be exactly same due to copyright. I have added details of our logo on new image uploaded and content that needs to be magnet. If you can present all 3 cards with seperate images in the one file that would be excellent.
Thank you

Please try and replicate all 3 images as close as possible with minimum 300 dpi. No writing required at all only images. If 3 images are too big for card size doesn't matter as I can use for 3 different cards. Thank you

```html
<!DOCTYPE html>
<html lang="en">
<head>
<meta charset="UTF-8">
<title>Optometry Business Cards</title>
<link rel="stylesheet" href="https://fonts.googleapis.com/css2?family=Lato:wght@300;700&family=Arimo:wght@700&display=swap">
<style>
  :root {
    --backdrop: #ececec;
    --pink-deep: #c72f70;
    --pink-mid: #c86a89;
    --pink-soft: #d29aae;
    --cream: #f1e6e2;
    --fur: #e9dcd6;
    --ink-light: #ffffff;
    --tagline: #c42a73;
  }
  * { margin: 0; padding: 0; box-sizing: border-box; }
  html, body { width: 1200px; height: 782px; overflow: hidden; }
  body { background: var(--backdrop); position: relative; }

  .card {
    position: absolute;
    overflow: hidden;
    background: linear-gradient(180deg, var(--pink-deep) 0%, var(--pink-mid) 45%, var(--pink-soft) 100%);
    box-shadow: 0 4px 14px rgba(0,0,0,0.18);
  }
  .card--landscape { left: 136px; top: 340px; width: 550px; height: 310px; }
  .card--portrait  { left: 710px; top: 84px;  width: 326px; height: 568px; }

  .photo-area { position: absolute; inset: 0; }
  .card--landscape .photo-area {
    background:
      radial-gradient(ellipse 40% 62% at 68% 50%, var(--fur) 0%, rgba(233,220,214,0.9) 45%, rgba(233,220,214,0) 100%),
      radial-gradient(ellipse 55% 35% at 72% 100%, var(--cream) 0%, rgba(241,230,226,0.7) 50%, rgba(241,230,226,0) 100%);
  }
  .card--portrait .photo-area {
    background:
      radial-gradient(ellipse 80% 30% at 50% 68%, var(--fur) 0%, rgba(233,220,214,0.88) 50%, rgba(233,220,214,0) 100%),
      radial-gradient(ellipse 90% 18% at 50% 100%, var(--cream) 0%, rgba(241,230,226,0.7) 50%, rgba(241,230,226,0) 100%);
  }

  .contact {
    position: absolute;
    text-align: center;
    color: var(--ink-light);
  }
  .card--landscape .contact { left: 0; width: 232px; top: 92px; }
  .card--portrait .contact  { left: 0; right: 0; top: 66px; }

  .contact__name {
    font-family: "Lato", sans-serif;
    font-weight: 700;
    font-size: 18.5px;
    letter-spacing: -0.2px;
    line-height: 22px;
  }
  .contact__address {
    font-family: "Lato", sans-serif;
    font-weight: 300;
    font-size: 16px;
    line-height: 18.5px;
    margin-top: 9px;
  }
  .contact__phone {
    font-family: "Lato", sans-serif;
    font-weight: 300;
    font-size: 16px;
    line-height: 18px;
    margin-top: 12px;
  }

  .tagline {
    position: absolute;
    right: 14px;
    bottom: 8px;
    font-family: "Arimo", sans-serif;
    font-weight: 700;
    font-size: 18px;
    color: var(--tagline);
  }
</style>
</head>
<body>

  <section class="card card--landscape">
    <div class="photo-area" role="img" aria-label="Photo of a white bulldog puppy wearing pink heart-shaped glasses, resting on a soft blanket"></div>
    <div class="contact">
      <p class="contact__name">DR CASEY HARTWELL</p>
      <p class="contact__address">1820 W. Larkspur<br>Mesa,AZ 85201</p>
      <p class="contact__phone">(480) 555-0147</p>
    </div>
    <p class="tagline">See all that you can see!</p>
  </section>

  <section class="card card--portrait">
    <div class="photo-area" role="img" aria-label="Photo of a white bulldog puppy wearing pink heart-shaped glasses, resting on a soft blanket"></div>
    <div class="contact">
      <p class="contact__name">DR CASEY HARTWELL</p>
      <p class="contact__address">1820 W. Larkspur<br>Mesa,AZ 85201</p>
      <p class="contact__phone">(480) 555-0147</p>
    </div>
    <p class="tagline">See all that you can see!</p>
  </section>

</body>
</html>
```